Business card design

We need a business card designed completed for a new company. We are a company that works with associations, schools to convert their older text/DVDs into dynamic online and mobile programs. Our initial platform is designed for the legal associations and will enable their lawyers to access their content such as forms, videos, case law and support materials anywhere, anytime. We are also focused on Project Management Associations, Financial Management Associations and IT Associations.

I would like for the business card to have the following information:

Logo

Kent marrowby

President and CEO

kmarrowby@trevantiq.example

Mobile: 555-374-9160

www.trevantiq.example

Tag line: Transforming content into a mobile platform    

I would like it to be double sided, use the colours of the logo, tie into the mobile world

 

Industry/Entity Type

Legal

Logo Text

Trevantiq

```html
<!DOCTYPE html>
<html lang="en">
<head>
<meta charset="utf-8">
<title>Trevantiq business card</title>
<link rel="stylesheet" href="https://fonts.googleapis.com/css2?family=Open+Sans:wght@400;600;700;800&display=swap">
<style>
  :root {
    --backdrop: #ece9e4;
    --label: #222222;
    --card-grey: #9b9b9b;
    --card-white: #ffffff;
    --band-dark: #626262;
    --swoosh-mid: #a5a5a5;
    --ink-light: #ffffff;
    --ink-dark: #5c5c5c;
    --ink-body: #3a3a3a;
  }
  * { margin: 0; padding: 0; box-sizing: border-box; }
  html, body {
    width: 1200px; height: 800px; overflow: hidden;
    background: var(--backdrop);
    font-family: "Open Sans", Arial, sans-serif;
  }
  .sheet { position: relative; width: 1200px; height: 800px; }
  .view-label {
    position: absolute; font-size: 21px; color: var(--label);
    text-align: center; width: 200px;
  }
  .card {
    position: absolute; width: 510px; height: 291px; border-radius: 18px;
    overflow: hidden;
  }
  .card--grey { background: var(--card-grey); color: var(--ink-light); }
  .card--white { background: var(--card-white); color: var(--ink-body); border: 1px solid #d8d8d8; }
  .card__art { position: absolute; inset: 0; width: 100%; height: 100%; }
  .brand-name {
    position: absolute; font-weight: 800; letter-spacing: -1px; line-height: 1;
    white-space: nowrap;
  }
  .card--grey .brand-name { color: var(--ink-light); }
  .card--white .brand-name { color: var(--ink-dark); }
  .details .brand-name { left: 33px; top: 20px; font-size: 68px; }
  .tagline { position: absolute; left: 33px; top: 112px; font-size: 15px; }
  .contact { position: absolute; left: 33px; top: 164px; font-size: 13px; line-height: 25px; }
  .contact__name { font-size: 15px; font-weight: 700; }
  .contact__role { font-size: 12.5px; font-weight: 400; }
  .contact__key { font-weight: 700; font-style: italic; }
  .card--grey .tagline, .card--grey .contact { color: var(--ink-light); }
  .card--grey .contact__name { color: #4a4a4a; }
  .card--grey .contact { color: #3d3d3d; }
  .card--grey .tagline { color: #f4f4f4; }
  .card--white .tagline { color: #666; }
  .reverse .brand-name {
    left: 0; right: 0; text-align: center; top: 92px; font-size: 86px;
  }
  .reverse .site {
    position: absolute; left: 0; right: 0; bottom: 18px; text-align: center;
    font-size: 16px; letter-spacing: 3px; font-weight: 600; color: #222;
  }
</style>
</head>
<body>
<main class="sheet">
  <div class="view-label" style="left:229px;top:48px;">Front</div>
  <div class="view-label" style="left:787px;top:48px;">Back - 1</div>
  <div class="view-label" style="left:233px;top:408px;">Back - 2</div>
  <div class="view-label" style="left:787px;top:408px;">Back - 3</div>

  <section class="card card--grey details" style="left:80px;top:97px;">
    <svg class="card__art" viewBox="0 0 510 291" aria-hidden="true">
      <path d="M405,0 C470,40 495,140 462,205 C442,245 420,270 398,291 L510,291 L510,0 Z" fill="var(--band-dark)"/>
      <path d="M468,112 C482,195 420,262 300,291 L398,291 C440,250 474,195 468,112 Z" fill="var(--card-white)"/>
    </svg>
    <div class="brand-name">Trevantiq</div>
    <p class="tagline">Transforming content, into a mobile platform</p>
    <div class="contact">
      <div><span class="contact__name">Kent marrowby,</span> <span class="contact__role">President and CEO</span></div>
      <div><span class="contact__key">C</span> : 555-374-9160</div>
      <div><span class="contact__key">E</span> : kmarrowby@trevantiq.example</div>
      <div><span class="contact__key">W</span> : www.trevantiq.example</div>
    </div>
  </section>

  <section class="card card--white details" style="left:642px;top:97px;">
    <svg class="card__art" viewBox="0 0 510 291" aria-hidden="true">
      <path d="M405,0 C470,40 495,140 462,205 C442,245 420,270 398,291 L510,291 L510,0 Z" fill="var(--band-dark)"/>
      <path d="M466,118 C478,198 418,262 300,291 L390,291 C432,250 470,195 466,118 Z" fill="var(--swoosh-mid)"/>
    </svg>
    <div class="brand-name">Trevantiq</div>
    <p class="tagline">Transforming content, into a mobile platform</p>
    <div class="contact">
      <div><span class="contact__name">Kent marrowby,</span> <span class="contact__role">President and CEO</span></div>
      <div><span class="contact__key">C</span> : 555-374-9160</div>
      <div><span class="contact__key">E</span> : kmarrowby@trevantiq.example</div>
      <div><span class="contact__key">W</span> : www.trevantiq.example</div>
    </div>
  </section>

  <section class="card card--grey reverse" style="left:73px;top:451px;">
    <div class="brand-name">Trevantiq</div>
    <p class="site">www.trevantiq.example</p>
  </section>

  <section class="card card--white reverse" style="left:634px;top:450px;">
    <div class="brand-name">Trevantiq</div>
    <p class="site">www.trevantiq.example</p>
  </section>
</main>
</body>
</html>
```